Federal Government Proposal Development Consulting company needs a website designed and coded

I am looking for someone to design (using an existing logo, color palette, and text fonts) and code a wordpress-based website for a Proposal Development consulting company. I have full copy for all site pages and suggestions for images/ graphics and a few example design templates to go from.

One note, from a color perspective - I included a mockup of a business card to highlight a color scheme that I tend to like - if you look at the back of the business card, the blend of the grey, blue, with the neon green highlight as a separator really seems to pop. Just a thought as you are designing the page.

I would like to see 2-3 potential design layouts, and I will select one to move forward with. Then, I would like the site to be coded for WordPress (I can provide a login to my wordpress site). I would like 1 opportunity to review the coded site and make any final tweaks.

```html
<!DOCTYPE html>
<html lang="en">
<head>
<meta charset="utf-8">
<title>Quillmark Consulting LLC — Proposal Development</title>
<link href="https://fonts.googleapis.com/css2?family=Tinos:wght@400;700&display=swap" rel="stylesheet">
<style>
:root{
  --navy:#0c1a4d;
  --blue:#0f58a5;
  --blue-deep:#0a3f86;
  --hero-a:#23497f;
  --hero-b:#0f2a55;
  --dark:#0a1f33;
  --dark-b:#06121f;
  --text:#3d3d3d;
  --muted:#6a6a6a;
  --line:#e4e4e4;
  --white:#ffffff;
  --black:#000000;
  --star:#f5b400;
}
*{margin:0;padding:0;box-sizing:border-box}
html,body{width:1200px;height:4545px;overflow:hidden}
body{position:relative;background:var(--white);font-family:"Tinos","Times New Roman",serif;color:var(--text)}
.abs{position:absolute}
a{color:inherit;text-decoration:none}
.btn{position:absolute;display:flex;align-items:center;justify-content:center;border-radius:20px;font-weight:700;font-size:14px}
.btn-blue{background:var(--blue);color:var(--white)}
.btn-white{background:var(--white);color:var(--navy)}
.h2{position:absolute;left:0;width:1200px;text-align:center;color:var(--navy);font-weight:700;font-size:42px}
.ph{position:absolute}

/* header */
.topline{left:0;top:0;width:1200px;height:6px;background:var(--blue-deep)}
.toptab{left:759px;top:0;width:317px;height:32px;background:var(--blue-deep);clip-path:polygon(0 0,100% 0,96% 100%,4% 100%);color:var(--white);font-size:12px;display:flex;align-items:center;justify-content:center;gap:8px}
.brand{left:111px;top:30px;display:flex;align-items:center;gap:10px;color:var(--navy);font-size:27px;line-height:1}
.brand small{display:block;font-size:14px;margin-top:4px;color:var(--muted)}
.brand .mark{width:14px;height:14px;background:var(--navy);border-radius:50%}
.nav{left:425px;top:72px;display:flex;gap:31px;font-size:14px;color:var(--navy)}
.callbtn{left:900px;top:64px;width:187px;height:38px;gap:10px;font-weight:400}
.header-rule{left:0;top:128px;width:1200px;height:1px;background:var(--line)}

/* hero */
.hero{left:0;top:129px;width:1200px;height:600px;background:linear-gradient(100deg,var(--hero-a) 0%,#1a3d72 45%,var(--hero-b) 100%)}
.hero-title{left:111px;top:300px;color:var(--white);font-size:50px;font-weight:700}
.hero-sub{left:111px;top:378px;width:470px;color:var(--white);font-size:24px;line-height:35px}
.hero-cut{left:1094px;top:650px;width:106px;height:80px;background:var(--white);clip-path:polygon(100% 0,100% 100%,0 100%)}

/* what we do */
.intro{left:150px;width:900px;text-align:center;font-size:14px;line-height:25.6px;color:var(--text)}
.card-img{height:196px;width:291px}
.card-title{width:291px;text-align:center;color:var(--navy);font-size:21px;font-weight:700}
.card-text{width:291px;padding:0 22px;text-align:center;font-size:14px;line-height:26px;color:var(--muted)}

/* services */
.services{left:0;top:1606px;width:1200px;height:839px;background:linear-gradient(160deg,var(--dark) 0%,var(--dark-b) 100%)}
.services-cut{left:0;top:1606px;width:111px;height:80px;background:var(--white);clip-path:polygon(0 0,100% 0,0 100%)}
.svc{width:226px;height:232px;background:var(--white);text-align:center}
.svc .ico{margin:22px auto 0;width:72px;height:72px;border-radius:50%;background:var(--navy);display:flex;align-items:center;justify-content:center}
.svc h3{margin-top:18px;color:var(--navy);font-size:19px}
.svc p{margin:8px auto 0;width:196px;font-size:13.5px;line-height:22px;color:var(--muted)}

/* who */
.who-text{left:672px;width:415px;font-size:14px;line-height:24px;color:var(--text)}

/* expertise */
.exp-img{width:291px;height:196px}
.exp-cap{width:291px;text-align:center;color:var(--navy);font-size:20px;font-weight:700}
.arrow{width:36px;height:36px;border-radius:50%;background:var(--navy);display:flex;align-items:center;justify-content:center}

/* testimonials */
.tcard{width:313px;height:208px;background:var(--white);box-shadow:0 2px 12px rgba(0,0,0,.13);padding:34px 38px 0}
.tcard p{font-size:14px;line-height:25px;color:var(--text)}
.tperson{margin-top:20px;display:flex;align-items:center;gap:14px}
.avatar{width:52px;height:52px;border-radius:50%;background:linear-gradient(135deg,#c9b7a8,#8c7667)}
.tperson b{display:block;color:var(--navy);font-size:12px}
.tperson span{font-size:11px;color:var(--text)}
.stars{color:var(--star);font-size:11px;letter-spacing:1px}
.dot{width:9px;height:9px;border-radius:50%;background:#bdbdbd;top:3824px}

/* contact */
.footer{left:0;top:4113px;width:1200px;height:432px;background:var(--black)}
.form{left:111px;top:4054px;width:976px;height:113px;background:var(--white);border-radius:8px;box-shadow:0 2px 10px rgba(0,0,0,.12)}
.field{top:4093px;width:229px;height:39px;background:#eef0f4;border-radius:3px;display:flex;align-items:center;justify-content:space-between;padding:0 14px 0 24px;font-size:12px;color:#888}
.submit{left:898px;top:4093px;width:141px;height:39px;font-size:16px}

/* footer */
.f-brand{left:111px;top:4240px;color:var(--white);font-size:52px;line-height:1}
.f-brand small{display:block;font-size:24px;margin:6px 0 0 60px}
.f-col h4{color:var(--white);font-size:20px;margin-bottom:18px}
.f-col li{list-style:none;color:var(--white);font-size:13px;line-height:30px}
.contact-row{display:flex;gap:12px;color:var(--white);font-size:13px;line-height:20px;margin-bottom:16px}
.contact-row b{font-size:15px}
.f-rule{left:0;top:4493px;width:1200px;height:1px;background:#3a3a3a}
.copy{left:0;top:4514px;width:1200px;text-align:center;color:var(--white);font-size:12px}
</style>
</head>
<body>

<!-- header -->
<div class="abs topline"></div>
<div class="abs toptab"><a href="#">Contact Us</a>|<a href="#">Contact Support</a>|<a href="#">Log In</a></div>
<div class="abs brand"><span><span>Quillmark</span><small>Consulting LLC</small></span><span class="mark"></span></div>
<nav class="abs nav"><a href="#">Home</a><a href="#">Work with Us</a><a href="#">Work for Us</a><a href="#">About Us</a><a href="#">Contact</a></nav>
<a class="btn btn-blue callbtn" href="#"><svg width="14" height="14" viewBox="0 0 24 24"><path fill="#fff" d="M6.6 10.8a15 15 0 006.6 6.6l2.2-2.2c.3-.3.7-.4 1-.2 1.1.4 2.3.6 3.6.6.6 0 1 .4 1 1V20c0 .6-.4 1-1 1A17 17 0 013 4c0-.6.4-1 1-1h3.5c.6 0 1 .4 1 1 0 1.3.2 2.5.6 3.6.1.3 0 .7-.2 1z"/></svg>(555) 014-2387</a>
<div class="abs header-rule"></div>

<!-- hero -->
<div class="abs hero" role="img" aria-label="Businessman's open hand holding glowing orange gears inside a digital circle on a blue background"></div>
<h1 class="abs hero-title">Generate Success:</h1>
<p class="abs hero-sub">Fuel Innovation in Proposal Excellence with Quillmark! Click here to explore our services.</p>
<a class="btn btn-white" style="left:111px;top:510px;width:155px;height:39px" href="#">Get Started</a>
<div class="abs hero-cut"></div>

<!-- what we do -->
<h2 class="h2" style="top:808px">What We Do</h2>
<p class="abs intro" style="top:879px">Quillmark, specializes in advancing an organization through a comprehensive suite of services designed to modernize the proposal development process. From innovative Capture Management strategies that pinpoint lucrative opportunities, meticulous Proposal Development services that transform concepts into effective narratives, and cutting-edge Generative AI techniques that create domain-aware content accelerating proposal draft development, we are your dedicated partner in securing success. With a unique fusion of technical expertise and exceptional writing capabilities, we surpass industry standards and set new benchmarks for excellence.</p>
<p class="abs intro" style="top:1021px">Discover a dynamic approach to proposal consulting that goes beyond conventional boundaries—choose Quillmark for solutions that Enhance the quality of your work, Elevate your corporate advantage, and Expand your industry presence.</p>

<div class="ph card-img" style="left:111px;top:1115px;background:linear-gradient(180deg,#e8e8e6,#8d8f93)" role="img" aria-label="Team of business professionals standing together"></div>
<div class="ph card-img" style="left:454px;top:1115px;background:linear-gradient(180deg,#d9dee3,#5c6570)" role="img" aria-label="Presenter at a whiteboard in a meeting room"></div>
<div class="ph card-img" style="left:796px;top:1115px;background:linear-gradient(180deg,#6d9a5a,#1e2a22)" role="img" aria-label="Hands on a laptop with a glowing AI hologram"></div>
<h3 class="abs card-title" style="left:111px;top:1328px">Capture Management</h3>
<h3 class="abs card-title" style="left:454px;top:1328px">Proposal Development</h3>
<h3 class="abs card-title" style="left:796px;top:1328px">Generative AI</h3>
<p class="abs card-text" style="left:111px;top:1365px">Trust us to analyze the market, mitigate risks, and develop strategies that maximize the ability to secure lucrative opportunities.</p>
<p class="abs card-text" style="left:454px;top:1365px">Turn your ideas into persuasive documents that leave a lasting impression on clients to set you apart from the competition.</p>
<p class="abs card-text" style="left:796px;top:1365px">Revolutionize your proposal writing process with our domain-aware Generative AI services.</p>
<a class="btn btn-blue" style="left:179px;top:1483px;width:155px;height:37px" href="#">Read More</a>
<a class="btn btn-blue" style="left:522px;top:1483px;width:155px;height:37px" href="#">Read More</a>
<a class="btn btn-blue" style="left:864px;top:1483px;width:155px;height:37px" href="#">Read More</a>

<!-- services -->
<div class="abs services" role="img" aria-label="Dark blue business background with faint charts and technology graphics"></div>
<div class="abs services-cut"></div>
<h2 class="h2" style="top:1676px;color:var(--white)">Our Services</h2>

<div class="abs svc" style="left:111px;top:1786px"><div class="ico"><svg width="34" height="34" viewBox="0 0 24 24" fill="none" stroke="#fff" stroke-width="1.5"><circle cx="12" cy="12" r="6"/><path d="M12 2v4M12 18v4M2 12h4M18 12h4"/></svg></div><h3>Generative AI</h3><p>Excepteur sint occaecat in culpa qui officia deserunt mollit anim id est laborum.</p></div>
<div class="abs svc" style="left:362px;top:1786px"><div class="ico"><svg width="34" height="34" viewBox="0 0 24 24" fill="none" stroke="#fff" stroke-width="1.5"><circle cx="12" cy="10" r="4"/><path d="M4 20h16M8 16l-2 4M16 16l2 4"/></svg></div><h3>Technical Solutioning</h3><p>Excepteur sint occaecat in culpa qui officia deserunt mollit anim id est laborum.</p></div>
<div class="abs svc" style="left:611px;top:1786px"><div class="ico"><svg width="34" height="34" viewBox="0 0 24 24" fill="none" stroke="#fff" stroke-width="1.5"><rect x="4" y="5" width="14" height="12" rx="1"/><path d="M7 9h8M7 13h5"/></svg></div><h3>Capture Management</h3><p>Excepteur sint occaecat in culpa qui officia deserunt mollit anim id est laborum.</p></div>
<div class="abs svc" style="left:861px;top:1786px"><div class="ico"><svg width="34" height="34" viewBox="0 0 24 24" fill="none" stroke="#fff" stroke-width="1.5"><path d="M6 3h9l3 3v15H6z"/><path d="M9 9h6M9 13h6M9 17h4"/></svg></div><h3>Proposal Management</h3><p>Excepteur sint occaecat in culpa qui officia deserunt mollit anim id est laborum.</p></div>

<div class="abs svc" style="left:111px;top:2054px"><div class="ico"><svg width="34" height="34" viewBox="0 0 24 24" fill="none" stroke="#fff" stroke-width="1.5"><path d="M6 3h12v18H6z"/><path d="M9 12l2 2 4-4"/></svg></div><h3>Compliance Reviews</h3><p>Excepteur sint occaecat in culpa qui officia deserunt mollit anim id est laborum.</p></div>
<div class="abs svc" style="left:362px;top:2054px"><div class="ico"><svg width="34" height="34" viewBox="0 0 24 24" fill="none" stroke="#fff" stroke-width="1.5"><path d="M6 3h12v18H6z"/><path d="M9 7h6M9 11h6M9 15h3"/></svg></div><h3>Executive Summaries</h3><p>Excepteur sint occaecat in culpa qui officia deserunt mollit anim id est laborum.</p></div>
<div class="abs svc" style="left:611px;top:2054px"><div class="ico"><svg width="34" height="34" viewBox="0 0 24 24" fill="none" stroke="#fff" stroke-width="1.5"><circle cx="8" cy="9" r="3"/><circle cx="16" cy="9" r="3"/><path d="M3 19c1-3 3-5 5-5s4 2 5 5M11 19c1-3 3-5 5-5s4 2 5 5"/></svg></div><h3>Volume Lead</h3><p>Excepteur sint occaecat in culpa qui officia deserunt mollit anim id est laborum.</p></div>
<div class="abs svc" style="left:861px;top:2054px"><div class="ico"><svg width="34" height="34" viewBox="0 0 24 24" fill="none" stroke="#fff" stroke-width="1.5"><circle cx="12" cy="12" r="4"/><circle cx="12" cy="12" r="8" stroke-dasharray="3 2"/></svg></div><h3>Technical Writer</h3><p>Excepteur sint occaecat in culpa qui officia deserunt mollit anim id est laborum.</p></div>

<a class="btn btn-white" style="left:524px;top:2326px;width:154px;height:37px" href="#">View All</a>

<!-- who we are -->
<div class="ph" style="left:111px;top:2531px;width:496px;height:457px;background:linear-gradient(135deg,#eceae6,#a9a39b)" role="img" aria-label="Man and woman reviewing a document beside a laptop"></div>
<h2 class="abs" style="left:672px;top:2562px;color:var(--navy);font-size:42px;font-weight:700">Who We Are</h2>
<p class="abs who-text" style="top:2623px">Lorem ipsum dolor sit amet, consectetur adipiscing elit, sed do eiusmod tempor incididunt ut labore et dolore magna aliqua. Ut enim ad minim veniam, quis nostrud exercitation ullamco laboris nisi ut aliquip ex ea commodo consequat.</p>
<p class="abs who-text" style="top:2741px">Sed ut perspiciatis unde omnis iste natus error sit voluptatem accusantium doloremque laudantium, totam rem aperiam, eaque ipsa quae ab illo inventore veritatis et quasi architecto beatae vitae dicta sunt explicabo. Nemo enim ipsam voluptatem quia voluptas sit aspernatur aut odit aut fugit, sed quia consequuntur magni dolores eos qui ratione voluptatem sequi nesciunt.</p>
<a class="btn btn-blue" style="left:672px;top:2912px;width:155px;height:37px" href="#">About Us</a>

<!-- expertise -->
<h2 class="h2" style="top:3064px">Subject Matter Expertise</h2>
<div class="abs arrow" style="left:53px;top:3240px"><svg width="14" height="14" viewBox="0 0 24 24"><path d="M15 4L7 12l8 8" stroke="#fff" stroke-width="3" fill="none"/></svg></div>
<div class="abs arrow" style="left:1112px;top:3240px"><svg width="14" height="14" viewBox="0 0 24 24"><path d="M9 4l8 8-8 8" stroke="#fff" stroke-width="3" fill="none"/></svg></div>
<div class="ph exp-img" style="left:111px;top:3161px;background:linear-gradient(135deg,#9fb4c9,#2a4e73)" role="img" aria-label="Engineer holding a hard hat with technology overlay"></div>
<div class="ph exp-img" style="left:454px;top:3161px;background:linear-gradient(180deg,#3b8ad1,#0d2d5a)" role="img" aria-label="Server room corridor with cloud network icons"></div>
<div class="ph exp-img" style="left:796px;top:3161px;background:linear-gradient(180deg,#1f4fa8,#07142e)" role="img" aria-label="Laptop keyboard with data charts on screen"></div>
<h3 class="abs exp-cap" style="left:111px;top:3373px">Systems Engineering</h3>
<h3 class="abs exp-cap" style="left:454px;top:3373px">Systems Integration</h3>
<h3 class="abs exp-cap" style="left:796px;top:3373px">Data Analysis</h3>

<!-- testimonials -->
<h2 class="h2" style="top:3476px">Testimonials</h2>
<div class="abs tcard" style="left:111px;top:3569px"><p>Excepteur sint occaecat cupidatat non proident, sunt in culpa qui officia deserunt mollit anim id est laborum.</p><div class="tperson"><div class="avatar" role="img" aria-label="Client portrait"></div><div><b>Lorem Ipsum</b><span>It is a long established fact</span><div class="stars">★★★★★</div></div></div></div>
<div class="abs tcard" style="left:443px;top:3569px"><p>Excepteur sint occaecat cupidatat non proident, sunt in culpa qui officia deserunt mollit anim id est laborum.</p><div class="tperson"><div class="avatar" role="img" aria-label="Client portrait"></div><div><b>Lorem Ipsum</b><span>It is a long established fact</span><div class="stars">★★★★★</div></div></div></div>
<div class="abs tcard" style="left:775px;top:3569px"><p>Excepteur sint occaecat cupidatat non proident, sunt in culpa qui officia deserunt mollit anim id est laborum.</p><div class="tperson"><div class="avatar" role="img" aria-label="Client portrait"></div><div><b>Lorem Ipsum</b><span>It is a long established fact</span><div class="stars">★★★★★</div></div></div></div>
<div class="abs dot" style="left:574px"></div>
<div class="abs dot" style="left:591px;top:3821px;width:15px;height:15px;background:var(--navy)"></div>
<div class="abs dot" style="left:616px"></div>

<!-- contact -->
<h2 class="h2" style="top:3912px">Contact Us</h2>
<p class="abs intro" style="top:3978px;left:180px;width:840px">Lorem ipsum dolor sit amet, consectetur adipiscing elit, sed do eiusmod tempor incididunt ut labore et dolore magna aliqua. Ut enim ad minim veniam, quis nostrud exercitation aliquip ex ea commodo consequat.</p>
<div class="abs footer"></div>
<div class="abs form"></div>
<div class="abs field" style="left:157px">Enter Name<svg width="13" height="13" viewBox="0 0 24 24"><circle cx="12" cy="7" r="5" fill="var(--navy)"/><path d="M3 22c0-5 4-8 9-8s9 3 9 8z" fill="var(--navy)"/></svg></div>
<div class="abs field" style="left:402px">Enter Email<svg width="14" height="12" viewBox="0 0 24 18"><rect width="24" height="18" fill="var(--navy)"/><path d="M1 1l11 9 11-9" stroke="#fff" stroke-width="2" fill="none"/></svg></div>
<div class="abs field" style="left:648px">Enter Phone<svg width="13" height="13" viewBox="0 0 24 24"><path fill="var(--navy)" d="M6.6 10.8a15 15 0 006.6 6.6l2.2-2.2c.3-.3.7-.4 1-.2 1.1.4 2.3.6 3.6.6.6 0 1 .4 1 1V20c0 .6-.4 1-1 1A17 17 0 013 4c0-.6.4-1 1-1h3.5c.6 0 1 .4 1 1 0 1.3.2 2.5.6 3.6.1.3 0 .7-.2 1z"/></svg></div>
<a class="btn btn-blue submit" href="#">Submit</a>

<!-- footer -->
<div class="abs f-brand">Quillmark<small>Consulting LLC</small></div>
<div class="abs f-col" style="left:533px;top:4238px"><h4>Quick Links</h4><ul><li>Home</li><li>Work with Us</li><li>Work for Us</li><li>About Us</li><li>Contact</li></ul></div>
<div class="abs f-col" style="left:743px;top:4238px"><h4>Contact Details</h4>
  <div class="contact-row"><svg width="14" height="14" viewBox="0 0 24 24" style="margin-top:3px"><path fill="#fff" d="M6.6 10.8a15 15 0 006.6 6.6l2.2-2.2c.3-.3.7-.4 1-.2 1.1.4 2.3.6 3.6.6.6 0 1 .4 1 1V20c0 .6-.4 1-1 1A17 17 0 013 4c0-.6.4-1 1-1h3.5c.6 0 1 .4 1 1 0 1.3.2 2.5.6 3.6.1.3 0 .7-.2 1z"/></svg><div><b>Phone</b><br>(555) 014-2387</div></div>
  <div class="contact-row"><svg width="14" height="11" viewBox="0 0 24 18" style="margin-top:4px"><rect width="24" height="18" fill="#fff"/><path d="M1 1l11 9 11-9" stroke="#000" stroke-width="2" fill="none"/></svg><div><b>Email</b><br>info@quillmarkconsulting.example</div></div>
</div>
<div class="abs f-col" style="left:995px;top:4238px"><h4>Follow Us</h4><ul><li>Community</li><li>Newsfeed</li><li>Gallery</li><li>Network</li></ul></div>
<div class="abs f-rule"></div>
<p class="abs copy">Copyright © 2023 Quillmark Consulting. All rights reserved.</p>

</body>
</html>
```